Modern Verdell Tree Care Website

I need a website for a full service Tree Care company. The company provides tree pruning, tree removal, tree preservation, emergency services, stump grinding, and emergency tree services.

Target Market(s)

Customers that need tree services

Industry/Entity Type

Landscaping, Tree Services

Coding

Coded - Design and coding required

Number of Pages Required

5+ page

Font styles to use
Sans Serif

Requirements
Must have
• Good clean design that showcases the services the company provides.
Nice to have
• Services page; contact form, blog, home page, about page

```html
<!DOCTYPE html>
<html lang="en">
<head>
<meta charset="utf-8">
<title>Verdell Tree Care – Landing Page Mobile View</title>
<link rel="stylesheet" href="https://fonts.googleapis.com/css2?family=Open+Sans:wght@400;600;700;800&family=Inter:wght@500&display=swap">
<style>
:root{
  --bg:#efefef;
  --white:#ffffff;
  --forest:#2f5428;
  --lime:#7dc242;
  --taupe:#8c8282;
  --ink:#2b2b2b;
  --muted:#7b7b7b;
  --line:#e6e6e6;
  --slate:#56676a;
  --navy:#1d2340;
  --gold:#f2b705;
}
*{box-sizing:border-box;margin:0;padding:0}
html,body{width:1200px;height:1200px;overflow:hidden;background:var(--bg);font-family:"Open Sans",sans-serif;color:var(--ink)}
.canvas{position:relative;width:1200px;height:1200px}
.brand-block{position:absolute;left:40px;top:80px;width:270px}
.brand-name{display:flex;align-items:flex-start;gap:12px;font-weight:800;font-size:32px;line-height:1.1;color:var(--slate);letter-spacing:.3px}
.brand-mark{flex:none;width:28px;height:28px;margin-top:6px;background:var(--lime)}
.brand-caption{margin-top:22px;font-family:"Inter",sans-serif;font-weight:500;font-size:27px;line-height:1.25;color:var(--navy)}
.screen{position:absolute;width:260px;background:var(--white);border-radius:18px;overflow:hidden;box-shadow:0 10px 30px rgba(0,0,0,.08)}
.eyebrow{font-size:11px;color:var(--taupe);margin-bottom:6px}
.heading{font-weight:800;font-size:19px;line-height:1.2;color:var(--taupe)}
.heading em{font-style:normal;color:var(--lime)}
.body-copy{font-size:8.5px;line-height:1.6;color:var(--muted);margin-top:10px}
.pad{padding:20px}
/* form */
.form-card{margin-top:14px;border:1px solid var(--line);border-radius:10px;padding:14px}
.field-label{font-size:9px;color:var(--ink);margin:8px 0 4px}
.field{height:28px;border:1px solid var(--line);border-radius:6px;font-size:8.5px;color:var(--muted);padding:7px 8px}
.field.tall{height:80px}
.btn-submit{margin-top:14px;height:30px;border-radius:5px;background:var(--lime);color:#fff;font-size:10px;font-weight:700;display:flex;align-items:center;justify-content:center}
.footer-strip{height:56px;background:var(--forest);display:flex;align-items:center;padding:0 20px;color:#fff;font-weight:800;font-size:18px}
/* reviews */
.center{text-align:center}
.rating-card{margin:16px 10px 0;padding:14px;border-radius:8px;box-shadow:0 6px 18px rgba(0,0,0,.07);text-align:center}
.stars{color:var(--lime);font-size:16px;letter-spacing:4px}
.stars.small{font-size:10px;letter-spacing:2px}
.tiny{font-size:8px;color:var(--ink)}
.tiny u{font-weight:700}
.review-card{margin:14px 10px 0;padding:12px;border-radius:8px;box-shadow:0 6px 18px rgba(0,0,0,.07)}
.review-top{display:flex;justify-content:space-between;align-items:baseline;margin-top:4px}
.review-title{font-size:10px;font-weight:700}
.review-date{font-size:7px;color:var(--muted)}
.review-text{font-size:7.5px;color:var(--muted);margin-top:4px;line-height:1.5}
.review-author{font-size:7.5px;font-weight:700;margin-top:6px}
.contact-label{font-size:11px;color:var(--taupe);margin:18px 20px 0}
/* hero */
.hero{position:relative;height:400px;background:linear-gradient(160deg,#1f3b1c 0%,#3d6a33 45%,#6b8d4a 100%);color:#fff;padding:18px}
.hero-bar{display:flex;justify-content:space-between;align-items:center}
.hero-brand{display:flex;align-items:center;gap:6px;font-weight:800;font-size:12px}
.hero-brand i{width:10px;height:10px;background:var(--lime);display:block}
.hero-title{margin-top:60px;font-weight:800;font-size:21px;line-height:1.25;text-align:center}
.hero-copy{font-size:8.5px;line-height:1.6;text-align:center;margin-top:12px;opacity:.9}
.btn-outline{margin:18px auto 0;width:120px;height:32px;border:1.5px solid #fff;border-radius:18px;display:flex;align-items:center;justify-content:center;font-size:10px}
/* features */
.feature-list{list-style:none;padding:20px 18px 0}
.feature-list li{display:flex;align-items:center;gap:8px;font-size:11px;font-weight:700;color:var(--forest);margin-bottom:13px}
.photo{display:block}
/* footer screen */
.footer-screen{background:var(--forest);color:#fff;padding:20px}
.footer-brand{display:flex;align-items:center;gap:8px;font-weight:800;font-size:18px}
.footer-brand i{width:16px;height:16px;background:var(--lime);display:block}
.footer-sub{font-size:10px;margin-top:16px}
.socials{display:flex;gap:8px;margin-top:8px}
.socials span{width:16px;height:16px;border-radius:50%;background:#fff;display:block}
.divider{height:1px;background:rgba(255,255,255,.25);margin:14px -20px}
.footer-head{font-size:11px;font-weight:700;margin:10px 0 6px}
.footer-link{font-size:9px;margin-bottom:6px;opacity:.9}
.mail{display:flex;align-items:center;gap:6px;font-size:9px}
/* services */
.service-label{position:absolute;left:20px;right:20px;bottom:-14px;background:#fff;border-radius:4px;padding:10px;font-weight:800;font-size:12px;color:var(--forest);box-shadow:0 6px 16px rgba(0,0,0,.08)}
</style>
</head>
<body>
<main class="canvas">

  <header class="brand-block">
    <div class="brand-name"><span class="brand-mark"></span><span>Verdell<br>Tree Care</span></div>
    <p class="brand-caption">Landing Page<br>Mobile view</p>
  </header>

  <!-- About -->
  <section class="screen" style="left:40px;top:300px;height:560px">
    <div class="pad">
      <p class="eyebrow">Who we are</p>
      <h2 class="heading">Committed to <em>Growing Greener</em> Communities</h2>
      <p class="body-copy">At Verdell Tree Care, we are more than just a tree service company; we are stewards of our beautiful trees. With a passion deeply rooted in arboriculture, we embark on a mission to promote the health, beauty, and safety of your trees and landscapes. Whether it's expert tree trimming to enhance aesthetics, meticulous tree removal to mitigate hazards, or comprehensive tree health assessments to ensure safety, we approach each task with unwavering dedication and attention to detail.</p>
    </div>
    <div class="photo" role="img" aria-label="Misty evergreen forest" style="height:260px;background:linear-gradient(180deg,#e9e6e8 0%,#9bb09e 35%,#2f5a38 70%,#1f3f26 100%)"></div>
  </section>

  <!-- Contact form -->
  <section class="screen" style="left:330px;top:40px;height:520px">
    <div class="pad">
      <h2 class="heading">Tree Care <em>Specialists</em></h2>
      <p class="body-copy" style="margin-top:4px">Morem ipsum dolor sit amet, consectetur adipiscing elit.</p>
      <form class="form-card">
        <p class="field-label">Name</p><div class="field">Your name</div>
        <p class="field-label">Email</p><div class="field">Email</div>
        <p class="field-label">Phone</p><div class="field">phone number</div>
        <p class="field-label">Message</p><div class="field tall">write message</div>
        <div class="btn-submit">Submit</div>
      </form>
    </div>
    <div class="footer-strip">Verdell</div>
  </section>

  <!-- Hero -->
  <section class="screen" style="left:330px;top:580px;height:580px">
    <div class="hero" role="img" aria-label="Gardener tending lush ferns">
      <div class="hero-bar">
        <span class="hero-brand"><i></i>Verdell Tree Care</span>
        <svg width="14" height="12" viewBox="0 0 14 12"><path d="M0 1h14M0 6h14M0 11h14" stroke="#f2b705" stroke-width="1.6"/></svg>
      </div>
      <h1 class="hero-title">Call Verdell for All Your Tree Care Needs</h1>
      <p class="hero-copy">Porem ipsum dolor sit amet, consectetur adipiscing elit. Nunc vulputate libero et velit interdum, ac aliquet odio mattis. Class aptent taciti sociosqu ad litora torquent per conubia nostra, per inceptos himenaeos.</p>
      <div class="btn-outline">Contact us</div>
    </div>
    <div class="pad">
      <p class="eyebrow">Who we are</p>
      <h2 class="heading">Committed to <em>Growing Greener</em></h2>
    </div>
  </section>

  <!-- Testimonials -->
  <section class="screen" style="left:620px;top:40px;height:520px">
    <div class="pad center" style="padding-bottom:0">
      <h2 class="heading">What <em>customers</em> say about us</h2>
      <p class="body-copy" style="margin-top:4px">We do our best to provide you the best experience ever</p>
    </div>
    <div class="rating-card">
      <p class="review-title">Excellent</p>
      <p class="stars">★★★★★</p>
      <p class="tiny">Based on <u>456 reviews</u></p>
      <p class="tiny" style="margin-top:4px"><span style="color:var(--lime)">★</span> ReviewNest</p>
    </div>
    <div class="review-card">
      <p class="stars small">★★★★★</p>
      <div class="review-top"><span class="review-title">Best on the market</span><span class="review-date">2 days ago</span></div>
      <p class="review-text">I love this product because the support is great. Please ...</p>
      <p class="review-author">Oakwanderer</p>
    </div>
    <p class="contact-label">Contact</p>
  </section>

  <!-- Features -->
  <section class="screen" style="left:620px;top:580px;height:580px">
    <ul class="feature-list">
      <li><svg width="12" height="10" viewBox="0 0 12 10"><path d="M1 5l3 3 7-7" stroke="#f2b705" stroke-width="2" fill="none"/></svg>Licensed and Insured</li>
      <li><svg width="12" height="10" viewBox="0 0 12 10"><path d="M1 5l3 3 7-7" stroke="#f2b705" stroke-width="2" fill="none"/></svg>24-Hours Emergency Services</li>
      <li><svg width="12" height="10" viewBox="0 0 12 10"><path d="M1 5l3 3 7-7" stroke="#f2b705" stroke-width="2" fill="none"/></svg>Locally Owned &amp; Operated</li>
      <li><svg width="12" height="10" viewBox="0 0 12 10"><path d="M1 5l3 3 7-7" stroke="#f2b705" stroke-width="2" fill="none"/></svg>Professional Work</li>
      <li><svg width="12" height="10" viewBox="0 0 12 10"><path d="M1 5l3 3 7-7" stroke="#f2b705" stroke-width="2" fill="none"/></svg>Safety is Our No.1 Priority</li>
      <li><svg width="12" height="10" viewBox="0 0 12 10"><path d="M1 5l3 3 7-7" stroke="#f2b705" stroke-width="2" fill="none"/></svg>Free Estimates</li>
      <li><svg width="12" height="10" viewBox="0 0 12 10"><path d="M1 5l3 3 7-7" stroke="#f2b705" stroke-width="2" fill="none"/></svg>Licensed Arborist on Staff</li>
    </ul>
    <div class="photo" role="img" aria-label="Arborist in safety gear trimming a tree" style="margin:10px 20px 0;height:250px;border-radius:40px;background:radial-gradient(circle at 50% 50%,#d9e86a 0%,#8cb83e 45%,#4f7f2a 100%)"></div>
  </section>

  <!-- Footer -->
  <section class="screen footer-screen" style="left:910px;top:40px;height:520px">
    <div class="footer-brand"><i></i>Verdell Tree Care</div>
    <p class="footer-sub">Get In Touch</p>
    <div class="socials"><span></span><span></span><span></span></div>
    <div class="divider"></div>
    <p class="footer-head">Pages</p>
    <p class="footer-link">Home</p><p class="footer-link">About</p><p class="footer-link">Service</p><p class="footer-link">Blog</p>
    <p class="footer-head">Legal</p>
    <p class="footer-link">Imprint</p><p class="footer-link">Terms&amp; Condition</p><p class="footer-link">Privacy</p><p class="footer-link">Cookies</p>
    <p class="footer-head">Contact Info</p>
    <p class="mail"><svg width="12" height="9" viewBox="0 0 12 9"><rect x=".5" y=".5" width="11" height="8" fill="none" stroke="#fff"/><path d="M.5 .5l5.5 4.5 5.5-4.5" fill="none" stroke="#fff"/></svg>hello@verdelltree.example</p>
  </section>

  <!-- Services -->
  <section class="screen" style="left:910px;top:580px;height:580px">
    <div class="pad center" style="padding-bottom:10px">
      <h2 class="heading">Quality <em>Services</em> Every Time</h2>
      <p class="body-copy" style="margin-top:4px">Morem ipsum dolor sit amet, consectetur adipiscing elit.</p>
    </div>
    <div style="position:relative;margin:0 20px">
      <div class="photo" role="img" aria-label="Arborist in a bucket lift trimming tall trees" style="height:300px;border-radius:8px;background:linear-gradient(180deg,#5a8fd6 0%,#6aa04a 45%,#2f6a2a 100%)"></div>
      <div class="service-label">Tree Trimming</div>
    </div>
    <div class="pad" style="margin-top:20px">
      <p class="eyebrow">Why Choose Us</p>
      <h2 class="heading"><em>Exceptional Care</em></h2>
    </div>
  </section>

</main>
</body>
</html>
```